New Company Business Card design

Looking for a corporate looking business card utilising my new logo design - the logo i would like embossed as one option and flat as another - simplistic but stylish - less is more - we are an import export business launching into the market - i would like a couple of options as main background - Grey or Black

```html
<!DOCTYPE html>
<html lang="en">
<head>
<meta charset="utf-8">
<title>Meridian Trade Partners – Business Card</title>
<link href="https://fonts.googleapis.com/css2?family=Open+Sans:wght@400;600;700&display=swap" rel="stylesheet">
<style>
  :root {
    --page-bg: #e9eaec;
    --card-bg: #ffffff;
    --brand-blue: #2f74c0;
    --brand-grey: #8a8b8d;
    --ink: #2b2b2b;
    --rule: #9a9a9a;
  }
  * { box-sizing: border-box; margin: 0; padding: 0; }
  html, body {
    width: 1200px; height: 900px; overflow: hidden;
    background: var(--page-bg);
    font-family: "Open Sans", Arial, sans-serif;
    color: var(--ink);
  }
  .sheet {
    position: relative; width: 1200px; height: 900px;
    display: flex; flex-direction: column; align-items: center; justify-content: center; gap: 56px;
  }
  .card {
    position: relative; width: 640px; height: 366px;
    background: var(--card-bg); border-radius: 18px; overflow: hidden;
    box-shadow: 0 6px 18px rgba(0,0,0,.12);
  }
  .card__band { position: absolute; left: 0; right: 0; bottom: 0; height: 9px; display: flex; }
  .card__band-blue { flex: 0 0 66%; background: var(--brand-blue); }
  .card__band-grey { flex: 1; background: var(--brand-grey); }

  .brand { display: inline-flex; flex-direction: column; align-items: stretch; white-space: nowrap; }
  .brand__row { display: flex; align-items: center; gap: 10px; }
  .brand__dot { width: 22px; height: 22px; border-radius: 50%; background: var(--brand-blue); flex: none; }
  .brand__name {
    color: var(--brand-blue); font-weight: 600; font-size: 21px; letter-spacing: .5px;
    text-transform: uppercase; line-height: 1.1;
  }
  .brand__tagline {
    margin-top: 6px; padding-top: 4px; border-top: 1px solid var(--rule);
    color: var(--brand-grey); font-size: 9.5px; letter-spacing: 2.6px; text-transform: uppercase;
  }

  /* front */
  .card--front .brand { position: absolute; left: 36px; top: 140px; }
  .card--front .divider {
    position: absolute; left: 36px; right: 36px; top: 206px; height: 1px; background: var(--rule);
  }
  .person { position: absolute; right: 36px; top: 52px; text-align: right; }
  .person__name { color: var(--brand-blue); font-weight: 700; font-size: 16px; text-transform: uppercase; }
  .person__title { font-size: 13px; margin-top: 2px; }
  .address {
    position: absolute; right: 36px; top: 124px; text-align: right;
    font-size: 14px; line-height: 1.45; font-style: normal;
  }

  .contacts { position: absolute; left: 36px; bottom: 30px; list-style: none; }
  .contacts li { display: flex; align-items: center; gap: 8px; font-size: 14.5px; line-height: 1.5; margin-top: 3px; white-space: nowrap; }
  .contacts svg { width: 16px; height: 16px; flex: none; }

  /* back */
  .card--back .brand { position: absolute; left: 50%; top: 50%; transform: translate(-50%, -60%); }
  .card--back .brand__name { font-size: 28px; }
  .card--back .brand__dot { width: 28px; height: 28px; }
  .card--back .brand__tagline { font-size: 11.5px; letter-spacing: 4px; text-align: center; }
</style>
</head>
<body>
<main class="sheet">
  <section class="card card--front" aria-label="Business card front">
    <div class="brand">
      <div class="brand__row"><span class="brand__dot"></span><span class="brand__name">Meridian Trade Partners</span></div>
      <div class="brand__tagline">Reliable supply for every market</div>
    </div>
    <div class="divider"></div>
    <div class="person">
      <div class="person__name">Daniel Archer</div>
      <div class="person__title">Founder/President</div>
    </div>
    <address class="address">P.O. Box 48, Harbour Road,<br>Eastport, 40517</address>
    <ul class="contacts">
      <li>
        <svg viewBox="0 0 16 16" aria-hidden="true"><rect width="16" height="16" rx="2" fill="var(--brand-blue)"/><path d="M5 4h2l1 2.5-1.2.8a6 6 0 0 0 2 2l.8-1.2L12 9v2a1 1 0 0 1-1 1A7 7 0 0 1 4 5a1 1 0 0 1 1-1z" fill="#fff"/></svg>
        (555) 014-2290
      </li>
      <li>
        <svg viewBox="0 0 16 16" aria-hidden="true"><rect width="16" height="16" rx="2" fill="var(--brand-blue)"/><rect x="3" y="5" width="10" height="7" fill="#fff"/><path d="M3 5l5 4 5-4" fill="none" stroke="var(--brand-blue)" stroke-width="1"/></svg>
        hello@meridiantrade.example
      </li>
      <li>
        <svg viewBox="0 0 16 16" aria-hidden="true"><rect width="16" height="16" rx="2" fill="var(--brand-blue)"/><circle cx="8" cy="8" r="4.5" fill="none" stroke="#fff" stroke-width="1.1"/><ellipse cx="8" cy="8" rx="2" ry="4.5" fill="none" stroke="#fff" stroke-width="1"/><path d="M3.5 8h9" stroke="#fff" stroke-width="1"/></svg>
        www.meridiantrade.example
      </li>
    </ul>
    <div class="card__band"><span class="card__band-blue"></span><span class="card__band-grey"></span></div>
  </section>

  <section class="card card--back" aria-label="Business card back">
    <div class="brand">
      <div class="brand__row"><span class="brand__dot"></span><span class="brand__name">Meridian Trade Partners</span></div>
      <div class="brand__tagline">Reliable supply for every market</div>
    </div>
    <div class="card__band"><span class="card__band-blue"></span><span class="card__band-grey"></span></div>
  </section>
</main>
</body>
</html>
```